Billboard design 8x3M RAVU (Spanish company)

We´re located in the south of Spain. We run a local telecom company.
We sell Fiber optic, and mobile phone lines mainly.
The billboard will have to be in Spanish, I would like the price to be something you spot on first sight when passing by in the car.
Our company color is blue, like in our logo which I will add. I will also add a example from what we currently have.
The new offer should be:
1000 megas + 100Gigas movil con llamadas ilimitadas. (meaning 1000Mb fiber optic speed and 100Gb data and unlimited calls for 1 mobile line)
Our details are: phone line 958 47 6620
Website: ra-vu.es

```html
<!DOCTYPE html>
<html lang="es">
<head>
<meta charset="utf-8">
<title>RAVU – Valla 1000 Megas</title>
<link rel="stylesheet" href="https://fonts.googleapis.com/css2?family=Montserrat:wght@700;800&family=Open+Sans:wght@400;600&family=Encode+Sans+Condensed:wght@400&display=swap">
<style>
  :root{
    --stage:#d5d4d2;
    --navy:#053550;
    --mid:#0a82c0;
    --sky:#2fb0ea;
    --band:#38b7ee;
    --orange:#ffad00;
    --white:#ffffff;
    --fire-1:#ff9a1a;
    --fire-2:#e8541a;
  }
  *{margin:0;padding:0;box-sizing:border-box}
  html,body{width:1200px;height:1106px;overflow:hidden;background:var(--stage)}
  .billboard{
    position:absolute;left:103px;width:995px;height:447px;overflow:hidden;
    background:linear-gradient(100deg,var(--navy) 0%,#07567f 22%,var(--mid) 45%,var(--sky) 75%,#34b4ec 100%);
  }
  .billboard--top{top:90px}
  .billboard--bottom{top:586px}
  .contact-band{position:absolute;left:0;bottom:0;width:100%;height:60px;background:var(--band)}
  .headline{position:absolute;left:40px;font-family:"Montserrat",sans-serif;font-weight:800;color:var(--white);white-space:nowrap;line-height:1}
  .headline .accent{color:var(--orange)}
  .headline--fiber{top:14px;font-size:90px;letter-spacing:-1px}
  .headline--fiber .accent{margin-left:4px}
  .headline--mobile{top:110px;font-size:74px;letter-spacing:-1px}
  .headline--mobile .plain{font-weight:700}
  .subline{position:absolute;left:40px;top:188px;font-family:"Open Sans",sans-serif;font-size:44px;color:var(--white);line-height:1}
  .english-note{position:absolute;left:39px;top:255px;width:260px;font-family:"Encode Sans Condensed",sans-serif;font-size:23px;line-height:30px;color:var(--orange)}
  .rule{position:absolute;left:37px;top:347px;width:253px;height:14px;border-radius:7px;background:var(--white)}
  .price{position:absolute;left:295px;top:246px;width:348px;height:127px;border-radius:32px;background:var(--orange);
    font-family:"Montserrat",sans-serif;font-weight:800;color:var(--white);white-space:nowrap}
  .price .por{position:absolute;left:22px;bottom:18px;font-size:52px;line-height:1;letter-spacing:-1px}
  .price .amount{position:absolute;left:116px;bottom:12px;font-size:126px;line-height:1;letter-spacing:-6px}
  .brand{position:absolute;left:745px;top:14px;font-family:"Montserrat",sans-serif;font-weight:800;font-size:66px;line-height:1;color:var(--white);letter-spacing:4px}
  .services{position:absolute;left:746px;top:80px;font-family:"Montserrat",sans-serif;font-weight:700;font-size:19px;color:var(--white);white-space:nowrap}
  .hero-art{position:absolute;left:550px;top:75px;width:390px;height:315px;
    background:radial-gradient(ellipse 55% 60% at 58% 55%,var(--fire-1) 0%,var(--fire-2) 55%,rgba(232,84,26,0) 100%)}
  .contact{position:absolute;left:117px;top:392px;display:flex;align-items:center;gap:10px;
    font-family:"Open Sans",sans-serif;font-size:46px;color:var(--white);line-height:1;white-space:nowrap}
  .contact svg{width:42px;height:42px;flex:none}
  .contact .web-icon{margin-left:14px}
</style>
</head>
<body>

<section class="billboard billboard--top">
  <div class="contact-band"></div>
  <div class="hero-art" role="img" aria-label="Cohete despegando de un portátil entre nubes de humo naranja"></div>
  <h1 class="headline headline--fiber">1000<span class="accent">Megas</span></h1>
  <h2 class="headline headline--mobile">+ 100<span class="accent">Gigas</span> <span class="plain">Movil</span></h2>
  <p class="subline">con llamadas ilimitadas</p>
  <p class="english-note">1000Mb fiber optic speed + 100Gb data and unlimited calls for1Mobile line</p>
  <div class="rule"></div>
  <div class="price"><span class="por">por</span><span class="amount">25€</span></div>
  <div class="brand">RAVU</div>
  <div class="services">Wifi | Fibra | Movil | Tv</div>
  <div class="contact">
    <svg viewBox="0 0 42 42" aria-hidden="true"><circle cx="21" cy="21" r="21" fill="#fff"/><path d="M14 11c2-1 3 0 4 3l1 3c0 1-1 2-2 3 1 3 3 5 6 6 1-1 2-2 3-2l3 1c3 1 4 2 3 4-1 3-4 4-7 3-6-2-11-7-13-13-1-3 0-6 2-8z" fill="#0a82c0"/><path d="M24 12a7 7 0 0 1 6 6M24 8a11 11 0 0 1 10 10" stroke="#0a82c0" stroke-width="2" fill="none" stroke-linecap="round"/></svg>
    <span>958 47 66 20</span>
    <svg class="web-icon" viewBox="0 0 42 42" aria-hidden="true"><circle cx="21" cy="21" r="20" fill="none" stroke="#fff" stroke-width="2"/><circle cx="21" cy="21" r="15" fill="none" stroke="#fff" stroke-width="2"/><ellipse cx="21" cy="21" rx="7" ry="15" fill="none" stroke="#fff" stroke-width="2"/><path d="M6 21h30M8 14h26M8 28h26M21 6v30" stroke="#fff" stroke-width="2"/></svg>
    <span>www.ra-vu.es</span>
  </div>
</section>

<section class="billboard billboard--bottom">
  <div class="contact-band"></div>
  <div class="hero-art" role="img" aria-label="Cohete despegando de un portátil entre nubes de humo naranja"></div>
  <h1 class="headline headline--fiber">1000<span class="accent">Megas</span></h1>
  <h2 class="headline headline--mobile">+ 100<span class="accent">Gigas</span> <span class="plain">Movil</span></h2>
  <p class="subline">con llamadas ilimitadas</p>
  <p class="english-note">1000Mb fiber optic speed + 100Gb data and unlimited calls for1Mobile line</p>
  <div class="rule"></div>
  <div class="price"><span class="por">por</span><span class="amount">25€</span></div>
  <div class="brand">RAVU</div>
  <div class="services">Wifi | Fibra | Movil | Tv</div>
  <div class="contact">
    <svg viewBox="0 0 42 42" aria-hidden="true"><circle cx="21" cy="21" r="21" fill="#fff"/><path d="M14 11c2-1 3 0 4 3l1 3c0 1-1 2-2 3 1 3 3 5 6 6 1-1 2-2 3-2l3 1c3 1 4 2 3 4-1 3-4 4-7 3-6-2-11-7-13-13-1-3 0-6 2-8z" fill="#0a82c0"/><path d="M24 12a7 7 0 0 1 6 6M24 8a11 11 0 0 1 10 10" stroke="#0a82c0" stroke-width="2" fill="none" stroke-linecap="round"/></svg>
    <span>958 47 66 20</span>
    <svg class="web-icon" viewBox="0 0 42 42" aria-hidden="true"><circle cx="21" cy="21" r="20" fill="none" stroke="#fff" stroke-width="2"/><circle cx="21" cy="21" r="15" fill="none" stroke="#fff" stroke-width="2"/><ellipse cx="21" cy="21" rx="7" ry="15" fill="none" stroke="#fff" stroke-width="2"/><path d="M6 21h30M8 14h26M8 28h26M21 6v30" stroke="#fff" stroke-width="2"/></svg>
    <span>www.ra-vu.es</span>
  </div>
</section>

</body>
</html>
```